Birch Hauling Business Card Design Project

We need a new company business card. We provide professional timber harvesting (logging) and forest management services. I'm open to any creative design. Most company caps and shirts are navy blue and Light grey. Logo does not necessarily have to contain those colors. Logo containing picture of logging equipment, log truck, trees, or logs are acceptable. Be creative. Final logo should communicate our company's pride and professionalism in the East Texas Timber Industry.
Updates

Target Market(s)

Timber owners, sawmills, and forestry professionals

Industry/Entity Type

Business

Requirements
Must have
• Must have Contact Info.
Phone: 936-402-5917
address: PO Box 4830
New Waverly, Tx 77358
www.jmbirchhauling.example
jmbirchhauling@mailbox.example
Owner: Jared Marsh

Or design must leave room for this info.

```html
<!DOCTYPE html>
<html lang="en">
<head>
<meta charset="utf-8">
<title>Birch Hauling – Business Card</title>
<link rel="stylesheet" href="https://fonts.googleapis.com/css2?family=Michroma&display=swap">
<style>
  :root {
    --backdrop: #8d9091;
    --card: #ffffff;
    --brand-red: #e0262b;
    --brand-red-dark: #c81d22;
    --charcoal: #2a2a2c;
    --swoosh: #3a3a3c;
    --ink-light: #ffffff;
  }
  * { margin: 0; padding: 0; box-sizing: border-box; }
  html, body {
    width: 1200px; height: 771px; overflow: hidden;
    background: var(--backdrop);
    font-family: "Michroma", "Arial", sans-serif;
  }
  .business-card {
    position: absolute; left: 75px; top: 85px;
    width: 1050px; height: 600px;
    background: var(--card);
    overflow: hidden;
    box-shadow: 0 10px 30px rgba(0,0,0,.25);
  }
  .card-art { position: absolute; inset: 0; }
  .brand {
    position: absolute; left: 90px; top: 80px;
    display: flex; align-items: center; gap: 22px;
    color: var(--charcoal);
  }
  .brand-square { width: 34px; height: 34px; background: var(--brand-red); }
  .brand-name { line-height: 1.15; text-transform: uppercase; }
  .brand-owner { display: block; font-size: 24px; letter-spacing: 2px; }
  .brand-company { display: block; font-size: 40px; letter-spacing: 1px; }
  .contact-list {
    position: absolute; left: 48px; top: 318px;
    list-style: none; color: var(--ink-light);
    font-size: 14px; letter-spacing: 1px;
  }
  .contact-list li { display: flex; align-items: center; gap: 12px; height: 24px; }
  .contact-icon { width: 16px; height: 16px; flex: none; }
  .contact-indent { padding-left: 28px; }
  .owner-block {
    position: absolute; right: 56px; bottom: 44px;
    text-align: right; color: var(--ink-light); text-transform: uppercase;
  }
  .owner-name { font-size: 24px; letter-spacing: 2px; }
  .owner-title { font-size: 15px; letter-spacing: 4px; margin-top: 8px; }
</style>
</head>
<body>
  <div class="business-card">
    <svg class="card-art" width="1050" height="600" viewBox="0 0 1050 600" aria-hidden="true">
      <defs>
        <linearGradient id="band-gradient" x1="0" y1="0" x2="1" y2="1">
          <stop offset="0" stop-color="var(--brand-red)"/>
          <stop offset="1" stop-color="var(--brand-red-dark)"/>
        </linearGradient>
      </defs>
      <path class="swoosh" d="M0,222 C300,212 540,318 720,352 C530,330 300,250 0,252 Z" fill="var(--swoosh)"/>
      <path class="swoosh-line" d="M560,318 C620,335 680,346 740,352" stroke="var(--charcoal)" stroke-width="2" fill="none"/>
      <path class="red-band" d="M0,268 C300,258 560,370 1050,352 L1050,600 L0,600 Z" fill="url(#band-gradient)"/>
    </svg>

    <div class="brand">
      <span class="brand-square"></span>
      <span class="brand-name">
        <span class="brand-owner">Jared Marsh</span>
        <span class="brand-company">Birch Hauling</span>
      </span>
    </div>

    <ul class="contact-list">
      <li>
        <svg class="contact-icon" viewBox="0 0 16 16"><circle cx="8" cy="8" r="8" fill="#fff"/><path d="M8 3.5a3 3 0 0 0-3 3c0 2.2 3 6 3 6s3-3.8 3-6a3 3 0 0 0-3-3zm0 4.2a1.2 1.2 0 1 1 0-2.4 1.2 1.2 0 0 1 0 2.4z" fill="var(--brand-red)"/></svg>
        PO Box 4830,
      </li>
      <li class="contact-indent">New Waverly, TX 77358</li>
      <li>
        <svg class="contact-icon" viewBox="0 0 16 16"><circle cx="8" cy="8" r="8" fill="#fff"/><path d="M5.2 4h1.6l.8 2-1 .8a5 5 0 0 0 2.6 2.6l.8-1 2 .8v1.6c0 .4-.4.8-.8.8A6.8 6.8 0 0 1 4.4 4.8c0-.4.4-.8.8-.8z" fill="var(--brand-red)"/></svg>
        936-402-5917
      </li>
      <li>
        <svg class="contact-icon" viewBox="0 0 16 16"><circle cx="8" cy="8" r="8" fill="#fff"/><path d="M5.2 4h1.6l.8 2-1 .8a5 5 0 0 0 2.6 2.6l.8-1 2 .8v1.6c0 .4-.4.8-.8.8A6.8 6.8 0 0 1 4.4 4.8c0-.4.4-.8.8-.8z" fill="var(--brand-red)"/></svg>
        936-402-5918
      </li>
      <li>
        <svg class="contact-icon" viewBox="0 0 16 16"><circle cx="8" cy="8" r="8" fill="#fff"/><rect x="5" y="3.5" width="6" height="9" rx="1" fill="var(--brand-red)"/><rect x="6" y="4.8" width="4" height="5.6" fill="#fff"/></svg>
        936-402-5919
      </li>
      <li>
        <svg class="contact-icon" viewBox="0 0 16 16"><circle cx="8" cy="8" r="8" fill="#fff"/><rect x="4" y="5" width="8" height="6" fill="var(--brand-red)"/><path d="M4 5l4 3.2L12 5" stroke="#fff" stroke-width="1" fill="none"/></svg>
        jmbirchhauling@mailbox.example
      </li>
      <li>
        <svg class="contact-icon" viewBox="0 0 16 16"><circle cx="8" cy="8" r="8" fill="#fff"/><circle cx="8" cy="8" r="4.2" stroke="var(--brand-red)" stroke-width="1.2" fill="none"/><path d="M3.8 8h8.4M8 3.8c-2 2.4-2 6 0 8.4M8 3.8c2 2.4 2 6 0 8.4" stroke="var(--brand-red)" stroke-width="1" fill="none"/></svg>
        www.jmbirchhauling.example
      </li>
    </ul>

    <div class="owner-block">
      <p class="owner-name">Jared Marsh</p>
      <p class="owner-title">Owner / C.E.O</p>
    </div>
  </div>
</body>
</html>
```